Refresh Application User Interface

Brightmoor wishes to update the look of its business applications. Two representative forms are shown below. Please note, we are not considering changes in functionality or usability. Our goal is a cleaner, more contemporary design.

Industry/Entity Type

Business

```html
<!DOCTYPE html>
<html lang="en">
<head>
<meta charset="utf-8">
<title>Brightmoor – Purchase Order Lines</title>
<link href="https://fonts.googleapis.com/css2?family=Open+Sans:wght@400;600;700&family=Arimo:ital,wght@0,400;0,700;1,400&display=swap" rel="stylesheet">
<style>
:root{
  --page:#222222;
  --topbar:#111111;
  --tab:#3a3a3a;
  --tab-active:#7ab648;
  --green:#8dc63f;
  --green-dark:#6e9d33;
  --toolbar:#4b7db8;
  --toolbar-line:#6a95c8;
  --panel:#f4f4f4;
  --white:#ffffff;
  --grid-bar:#cfdcef;
  --border:#c8c8c8;
  --ink:#1a1a1a;
  --link:#1a33b0;
  --okgreen:#1d7a1d;
  --red:#e01010;
  --note:#f7e600;
  --msg:#fdfbe6;
  --msg-border:#ece7b5;
  --logo:#2e7dd0;
}
*{box-sizing:border-box;margin:0;padding:0}
html,body{width:1200px;height:897px;overflow:hidden;background:var(--page)}
.app{position:relative;width:1086px;height:812px;transform:scale(1.105);transform-origin:0 0;font-family:"Open Sans",Arial,sans-serif;color:var(--white)}
.abs{position:absolute}
/* top bar */
.topbar{left:0;top:0;width:1086px;height:27px;background:var(--topbar);font-size:13px;line-height:27px}
.topbar .who{left:19px}
.topbar .role{left:212px}
.topbar b{font-weight:700}
.toplinks{right:0;top:0;display:flex}
.toplinks span{padding:0 8px;border-left:1px solid #333}
/* main nav */
.mainnav{left:19px;top:40px;display:flex;gap:2px}
.mainnav span{background:var(--tab);height:29px;line-height:29px;padding:0 11px;font-size:15px;font-weight:600}
.mainnav .on{background:var(--tab-active)}
.logo{left:868px;top:30px;font-size:29px;font-weight:700;color:var(--logo);letter-spacing:1px}
.subnav{left:0;top:70px;width:1086px;height:29px;background:var(--green);display:flex;align-items:center;padding-left:20px;gap:4px;font-size:13.5px;font-weight:600}
.subnav span{padding:1px 7px;border-radius:3px}
.subnav .on{background:var(--white);color:var(--green-dark)}
.subnav .alt{background:var(--green-dark)}
.subnav .gap{margin-left:12px}
.title{left:18px;top:107px;font-size:21px;font-weight:700}
.viewtabs{right:18px;top:112px;display:flex;gap:2px}
.viewtabs span{background:var(--topbar);padding:0 9px;height:28px;line-height:28px;font-size:15px;font-weight:600;position:relative}
.viewtabs .on{background:var(--toolbar)}
.dot{position:absolute;right:1px;top:1px;width:8px;height:8px;border-radius:50%;background:var(--tab-active)}
/* toolbar */
.toolbar{left:18px;top:140px;width:1049px;height:28px;background:var(--toolbar);display:flex;align-items:center;font-size:13px}
.tool{height:28px;display:flex;align-items:center;gap:6px;padding:0 8px;border-right:1px solid var(--toolbar-line)}
.tool.sel{background:#3a6aa2}
.tool.dim{opacity:.45}
.tright{margin-left:auto;display:flex;align-items:center;height:28px}
.tright .tool{border:0;border-left:1px solid var(--toolbar-line)}
.apply{background:#5f8fc8;border:1px solid #9bbde4;border-radius:3px;height:22px}
/* panel */
.panel{left:18px;top:168px;width:1049px;height:619px;background:var(--panel)}
.orderbox{left:32px;top:180px;width:1022px;height:82px;background:#f8f8f8;border:1px solid #e2e2e2;color:var(--ink);font-size:12.5px}
.grid{left:31px;top:274px;width:1025px;height:465px;background:#f7f7f7;border:1px solid var(--border);font-family:Arimo,Arial,sans-serif;font-size:12px;color:var(--ink)}
.gridbar{left:0;top:0;width:100%;height:24px;background:var(--grid-bar);border-bottom:1px solid #b5c7e0}
.gb-ic{top:0;width:26px;height:24px;display:flex;align-items:center;justify-content:center;border-right:1px solid #b5c7e0}
.pager{right:0;top:0;height:24px;display:flex}
.pager span{border-left:1px solid #b5c7e0;padding:0 9px;line-height:24px;font-family:"Open Sans",sans-serif;font-size:12.5px}
.head{font-weight:700;font-size:12.5px;top:32px}
.row{left:0;width:100%;height:83px;background:var(--white);border-top:1px solid #e1e1e1}
.row.blank{background:#f3f3f3}
.in{position:absolute;height:21px;border:1px solid #8a8a8a;background:var(--white);padding:2px 4px;line-height:15px;white-space:nowrap;overflow:hidden;font-size:12px}
.sel-box{position:absolute;height:20px;border:1px solid #8a8a8a;background:var(--white);padding:2px 4px;line-height:15px}
.sel-box i{position:absolute;right:0;top:0;width:20px;height:18px;border-left:1px solid #8a8a8a;display:flex;align-items:center;justify-content:center}
.cb{position:absolute;width:14px;height:14px;border:1px solid #777;background:var(--white)}
.link{color:var(--link);text-decoration:underline}
.blue{color:var(--link)}
.red{color:var(--red)}
.it{font-style:italic}
.msgbar{left:31px;top:749px;width:1025px;height:27px;background:var(--msg);border:1px solid var(--msg-border);border-radius:3px;color:#333;font-size:14px;text-align:center;line-height:25px}
</style>
</head>
<body>
<div class="app">
  <div class="abs topbar">
    <span class="abs who">Logged In As <b>Dana Holt</b> <svg width="12" height="12" viewBox="0 0 12 12"><circle cx="6" cy="6" r="4.5" fill="none" stroke="#999" stroke-width="2.4" stroke-dasharray="2 1.5"/><circle cx="6" cy="6" r="1.5" fill="#999"/></svg></span>
    <span class="abs role">Current Role <b>administrator</b> <svg width="12" height="8" viewBox="0 0 12 8"><path d="M1 1l5 5 5-5" stroke="#aaa" stroke-width="2" fill="none"/></svg></span>
    <div class="abs toplinks"><span>Touch</span><span>New Tab</span><span>Help</span><span>Support</span><span>Log Out</span></div>
  </div>

  <nav class="abs mainnav"><span>Home</span><span>eSource</span><span class="on">eBuy</span><span>eRequest</span><span>eSell</span><span>eStock</span><span>ePlan</span><span>Preferences</span></nav>
  <div class="abs logo">BRIGHTMOOR</div>

  <nav class="abs subnav"><span class="on">Orders</span><span>Receipes</span><span>Shipments</span><span>Invoices</span><span class="gap">Pricing</span><span class="alt">Tables</span><span>Reports</span><span>Inquiries</span><span>Periodic Tasks</span><span>Workflows</span></nav>

  <h1 class="abs title">Purchase Order Lines</h1>
  <div class="abs viewtabs"><span>Header</span><span class="on">Lines<i class="dot"></i></span><span>Charges</span><span>Notes<i class="dot"></i></span></div>

  <div class="abs toolbar">
    <span class="tool"><svg width="16" height="16" viewBox="0 0 16 16"><path d="M11 4l-6 6a2 2 0 003 3l6-6a3.5 3.5 0 00-5-5L3 8" stroke="#fff" stroke-width="1.6" fill="none"/></svg></span>
    <span class="tool"><svg width="20" height="18" viewBox="0 0 20 18"><rect x="1" y="1" width="11" height="14" fill="none" stroke="#fff" stroke-width="1.5"/><circle cx="12" cy="10" r="3.5" fill="none" stroke="#fff" stroke-width="1.6"/><path d="M14.5 12.5l4 4" stroke="#fff" stroke-width="2"/></svg></span>
    <span class="tool sel"><svg width="20" height="16" viewBox="0 0 20 16"><path d="M3 12L9 4l8 8" stroke="#fff" stroke-width="1.5" fill="none"/><circle cx="3" cy="12" r="2.5" fill="#fff"/><circle cx="9" cy="4" r="2.5" fill="#fff"/><circle cx="17" cy="12" r="2.5" fill="#fff"/></svg></span>
    <span class="tool"><svg width="18" height="16" viewBox="0 0 18 16"><rect x="1" y="4" width="16" height="11" rx="1" fill="#fff"/><rect x="6" y="1" width="6" height="4" fill="none" stroke="#fff" stroke-width="1.5"/></svg></span>
    <span class="tool dim"><svg width="16" height="16" viewBox="0 0 16 16"><circle cx="8" cy="8" r="7" fill="#fff"/></svg></span>
    <span class="tool"><svg width="20" height="18" viewBox="0 0 20 18"><path d="M2 16L11 7M5 2l12 12M14 2l3 3-4 4-3-3z" stroke="#fff" stroke-width="2" fill="none"/></svg>View GL Accounts</span>
    <span class="tool"><svg width="20" height="18" viewBox="0 0 20 18"><rect x="1" y="2" width="13" height="13" fill="none" stroke="#fff" stroke-width="1.5"/><path d="M4 6h7M4 9h7" stroke="#fff" stroke-width="1.3"/><circle cx="15" cy="13" r="4" fill="#fff"/></svg>Post Order</span>
    <div class="tright">
      <span class="tool"><svg width="13" height="13" viewBox="0 0 13 13"><circle cx="5" cy="5" r="3.8" fill="none" stroke="#fff" stroke-width="1.6"/><path d="M8 8l4 4" stroke="#fff" stroke-width="2"/></svg>search</span>
      <span class="tool dim"><svg width="12" height="12" viewBox="0 0 12 12"><circle cx="6" cy="6" r="5.5" fill="#fff"/></svg>new</span>
      <span class="tool apply"><svg width="13" height="11" viewBox="0 0 13 11"><path d="M1 6l4 4 7-9" stroke="#fff" stroke-width="2.2" fill="none"/></svg>apply</span>
      <span class="tool"><svg width="12" height="12" viewBox="0 0 12 12"><circle cx="6" cy="6" r="5.5" fill="#fff"/><path d="M4 4l4 4M8 4l-4 4" stroke="#4b7db8" stroke-width="1.5"/></svg>delete</span>
      <span class="tool"><svg width="14" height="12" viewBox="0 0 14 12"><path d="M5 1L1 5l4 4M1 5h7a5 5 0 015 5" stroke="#fff" stroke-width="1.8" fill="none"/></svg>back</span>
    </div>
  </div>

  <div class="abs panel"></div>

  <section class="abs orderbox">
    <span class="abs" style="left:46px;top:14px">Order #</span>
    <span class="abs" style="left:98px;top:14px">100159</span>
    <span class="abs" style="left:218px;top:12px;color:var(--okgreen);font-size:14.5px">Regular Purchase Order</span>
    <span class="abs" style="left:816px;top:12px;color:#1537e0;font-size:14.5px">Hold For Completion</span>
    <span class="abs" style="left:214px;top:46px;width:360px;height:21px;background:#e8e8e8;padding:2px 4px">Harbor Clinical Supply Inc., Westfield MA</span>
  </section>

  <section class="abs grid">
    <div class="abs gridbar">
      <span class="abs gb-ic" style="left:0"><svg width="14" height="14" viewBox="0 0 14 14"><path d="M12 2H2l5 5-5 5h10" stroke="#111" stroke-width="2" fill="none"/></svg></span>
      <span class="abs gb-ic" style="left:31px"><svg width="14" height="14" viewBox="0 0 14 14"><rect x="1" y="4" width="8" height="9" fill="none" stroke="#111" stroke-width="1.4"/><rect x="5" y="1" width="8" height="9" fill="#fff" stroke="#111" stroke-width="1.4"/></svg></span>
      <span class="abs gb-ic" style="left:62px"><svg width="14" height="15" viewBox="0 0 14 15"><rect x="1" y="2" width="10" height="12" fill="none" stroke="#111" stroke-width="1.4"/><rect x="6" y="7" width="7" height="7" fill="#fff" stroke="#111" stroke-width="1.4"/></svg></span>
      <span class="abs gb-ic" style="left:93px"><svg width="16" height="14" viewBox="0 0 16 14"><path d="M1 3h14M1 7h14M1 11h14" stroke="#111" stroke-width="1.4"/><circle cx="5" cy="3" r="2" fill="#fff" stroke="#111"/><circle cx="11" cy="7" r="2" fill="#fff" stroke="#111"/><circle cx="6" cy="11" r="2" fill="#fff" stroke="#111"/></svg></span>
      <span class="abs gb-ic" style="left:124px"><svg width="15" height="15" viewBox="0 0 15 15"><circle cx="7.5" cy="7.5" r="7" fill="#f04a1a"/><path d="M5 5l5 5M10 5l-5 5" stroke="#fff" stroke-width="1.8"/></svg></span>
      <div class="abs pager"><span>|◂</span><span>◂◂</span><span>Page 1 of 1</span><span>▸▸</span><span>▸|</span></div>
    </div>

    <span class="abs head" style="left:5px">Line #</span>
    <span class="abs head" style="left:78px">Product</span>
    <span class="abs head" style="left:203px">Supplier Part#</span>
    <span class="abs head" style="left:346px">Open Qty</span>
    <span class="abs head" style="left:445px">Unit</span>
    <span class="abs head" style="left:551px">Unit Price</span>
    <span class="abs head" style="left:669px">Extended</span>
    <span class="abs head" style="left:799px">LI Type / Ship To</span>
    <span class="cb" style="left:995px;top:31px"></span>

    <div class="abs row" style="top:53px">
      <span class="abs link" style="left:11px;top:7px">10</span>
      <span class="in" style="left:79px;top:3px;width:130px">P-1200</span>
      <svg class="abs" style="left:213px;top:7px" width="14" height="14" viewBox="0 0 14 14"><circle cx="8" cy="5.5" r="4" fill="none" stroke="#2e6db8" stroke-width="1.8"/><path d="M5 9l-4 4" stroke="#2e6db8" stroke-width="2"/></svg>
      <span class="cb" style="left:247px;top:6px"></span>
      <span class="in" style="left:341px;top:3px;width:88px">1</span>
      <span class="sel-box" style="left:441px;top:4px;width:77px">Ea<i><svg width="10" height="7" viewBox="0 0 10 7"><path d="M1 1l4 4 4-4" stroke="#222" stroke-width="1.8" fill="none"/></svg></i></span>
      <span class="in" style="left:540px;top:3px;width:109px">$6.50</span>
      <span class="abs blue" style="left:666px;top:7px">$6.50</span>
      <span class="sel-box" style="left:787px;top:3px;width:179px">Receive&amp;Pay<i><svg width="10" height="7" viewBox="0 0 10 7"><path d="M1 1l4 4 4-4" stroke="#222" stroke-width="1.8" fill="none"/></svg></i></span>
      <span class="cb" style="left:995px;top:9px"></span>
      <span class="in blue" style="left:79px;top:26px;width:570px">Northmill 381420 - Brochure Paper, Ultra Smooth Text, 8 1/2" x 11", 28 lb., 96 Brightness</span>
      <span class="abs blue it" style="left:666px;top:30px">ALCH</span>
      <span class="sel-box" style="left:787px;top:26px;width:179px">&nbsp;<i><svg width="10" height="7" viewBox="0 0 10 7"><path d="M1 1l4 4 4-4" stroke="#222" stroke-width="1.8" fill="none"/></svg></i></span>
      <span class="abs" style="left:121px;top:54px">On Purchase Orders</span>
      <span class="abs link" style="left:246px;top:54px">30</span>
      <span class="abs" style="left:344px;top:54px">Available&nbsp; <span class="blue">0</span></span>
      <span class="abs red it" style="left:541px;top:53px;text-decoration:underline">Over Budget</span>
      <span class="abs red" style="left:666px;top:53px">Pending</span>
      <svg class="abs" style="left:797px;top:52px" width="20" height="21" viewBox="0 0 20 21"><path d="M1 1h18v14l-5 5H1z" fill="var(--note)" stroke="#7a6d00"/></svg>
      <svg class="abs" style="left:866px;top:53px" width="20" height="20" viewBox="0 0 20 20"><rect x="1" y="3" width="18" height="16" fill="#fff" stroke="#333"/><rect x="1" y="3" width="18" height="4" fill="#c03030"/><text x="10" y="16" font-size="7" text-anchor="middle" fill="#333" font-family="Arimo,sans-serif">22</text></svg>
    </div>

    <div class="abs row" style="top:136px">
      <span class="abs link" style="left:11px;top:7px">20</span>
      <span class="in" style="left:79px;top:3px;width:130px">P-1100</span>
      <svg class="abs" style="left:213px;top:7px" width="14" height="14" viewBox="0 0 14 14"><circle cx="8" cy="5.5" r="4" fill="none" stroke="#2e6db8" stroke-width="1.8"/><path d="M5 9l-4 4" stroke="#2e6db8" stroke-width="2"/></svg>
      <span class="cb" style="left:247px;top:6px"></span>
      <span class="in" style="left:341px;top:3px;width:88px">1</span>
      <span class="sel-box" style="left:441px;top:4px;width:77px">Ea<i><svg width="10" height="7" viewBox="0 0 10 7"><path d="M1 1l4 4 4-4" stroke="#222" stroke-width="1.8" fill="none"/></svg></i></span>
      <span class="in" style="left:540px;top:3px;width:109px">$5.00</span>
      <span class="abs blue" style="left:666px;top:7px">$5.00</span>
      <span class="sel-box" style="left:787px;top:3px;width:179px">Receive&amp;Pay<i><svg width="10" height="7" viewBox="0 0 10 7"><path d="M1 1l4 4 4-4" stroke="#222" stroke-width="1.8" fill="none"/></svg></i></span>
      <span class="cb" style="left:995px;top:9px"></span>
      <span class="in blue" style="left:79px;top:26px;width:570px">Clearwave 452610 - Recycled Laser Paper 1 case(2,500 count)&nbsp; - 24lb,&nbsp; 90 bright</span>
      <span class="abs blue it" style="left:666px;top:30px">ALCH</span>
      <span class="sel-box" style="left:787px;top:26px;width:179px">&nbsp;<i><svg width="10" height="7" viewBox="0 0 10 7"><path d="M1 1l4 4 4-4" stroke="#222" stroke-width="1.8" fill="none"/></svg></i></span>
      <span class="abs" style="left:121px;top:54px">On Purchase Orders</span>
      <span class="abs link" style="left:246px;top:54px">170</span>
      <span class="abs" style="left:344px;top:54px">Available&nbsp; <span class="blue">0</span></span>
      <span class="abs red it" style="left:541px;top:53px;text-decoration:underline">Over Budget</span>
      <span class="abs red" style="left:666px;top:53px">Pending</span>
      <svg class="abs" style="left:797px;top:52px" width="20" height="21" viewBox="0 0 20 21"><path d="M1 1h18v14l-5 5H1z" fill="var(--note)" stroke="#7a6d00"/></svg>
      <svg class="abs" style="left:866px;top:53px" width="20" height="20" viewBox="0 0 20 20"><rect x="1" y="3" width="18" height="16" fill="#fff" stroke="#333"/><rect x="1" y="3" width="18" height="4" fill="#c03030"/><text x="10" y="16" font-size="7" text-anchor="middle" fill="#333" font-family="Arimo,sans-serif">22</text></svg>
    </div>

    <div class="abs row blank" style="top:219px">
      <span class="in" style="left:8px;top:3px;width:60px"></span>
      <span class="in" style="left:79px;top:3px;width:130px"></span>
      <svg class="abs" style="left:213px;top:7px" width="14" height="14" viewBox="0 0 14 14"><circle cx="8" cy="5.5" r="4" fill="none" stroke="#2e6db8" stroke-width="1.8"/><path d="M5 9l-4 4" stroke="#2e6db8" stroke-width="2"/></svg>
      <span class="cb" style="left:247px;top:6px"></span>
      <span class="in" style="left:341px;top:3px;width:88px"></span>
      <span class="sel-box" style="left:441px;top:4px;width:77px">&nbsp;<i><svg width="10" height="7" viewBox="0 0 10 7"><path d="M1 1l4 4 4-4" stroke="#222" stroke-width="1.8" fill="none"/></svg></i></span>
      <span class="in" style="left:540px;top:3px;width:109px"></span>
      <span class="sel-box" style="left:787px;top:3px;width:179px">Receive&amp;Pay<i><svg width="10" height="7" viewBox="0 0 10 7"><path d="M1 1l4 4 4-4" stroke="#222" stroke-width="1.8" fill="none"/></svg></i></span>
      <span class="in" style="left:79px;top:26px;width:570px"></span>
      <span class="sel-box" style="left:787px;top:26px;width:179px">&nbsp;<i><svg width="10" height="7" viewBox="0 0 10 7"><path d="M1 1l4 4 4-4" stroke="#222" stroke-width="1.8" fill="none"/></svg></i></span>
    </div>
  </section>

  <div class="abs msgbar">Click Search, or enter property values and click Apply</div>
</div>
</body>
</html>
```